Business Card Design Project

Doctor, Pain Management. Need a new business card design with appointment info on the back. New address is 18 Corvell Road, Suite 304, Brisdale, NJ 07391. Right now I believe the rest of the information is staying the same.

```html
<!DOCTYPE html>
<html lang="en">
<head>
<meta charset="utf-8">
<title>Gentle Relief Pain Care – Business Card</title>
<link href="https://fonts.googleapis.com/css2?family=Gelasio:wght@400;700&display=swap" rel="stylesheet">
<style>
  :root{
    --backdrop:#dcdcdc;
    --paper:#ffffff;
    --olive:#4b4a40;
    --olive-dark:#3e3d35;
    --ink:#2c2c26;
    --on-dark:#efede4;
    --shadow:rgba(0,0,0,.18);
  }
  *{box-sizing:border-box;margin:0;padding:0}
  html,body{width:1200px;height:864px;overflow:hidden}
  body{background:var(--backdrop);font-family:"Gelasio",Georgia,serif;position:relative;color:var(--ink)}
  .card{position:absolute;width:640px;height:366px;background:var(--paper);box-shadow:0 6px 18px var(--shadow);overflow:hidden}

  /* Back: appointment side */
  .card--back{left:500px;top:50px;padding:26px 34px}
  .appt-title{position:absolute;left:300px;top:34px;font-size:30px;font-weight:400;color:var(--olive)}
  .pen-icon{position:absolute;left:250px;top:14px}
  .field{position:absolute;font-size:18px;display:flex;align-items:flex-end;gap:6px}
  .field .rule{border-bottom:1.5px solid var(--ink);height:18px}
  .field--for{left:34px;top:72px}
  .field--for .rule{width:540px}
  .field--date{left:34px;top:108px}
  .field--date .rule{width:520px}
  .days{position:absolute;left:34px;top:150px;display:flex;gap:14px;font-size:19px}
  .day{display:flex;align-items:center;gap:4px}
  .box{width:15px;height:15px;border:1.5px solid var(--ink);display:inline-block}
  .field--time{left:300px;top:188px}
  .field--time .rule{width:240px}
  .day-rule{position:absolute;left:34px;top:206px;width:250px;border-bottom:1.5px solid var(--ink)}
  .notice{position:absolute;left:180px;top:226px;width:430px;text-align:center;font-size:19px;line-height:1.2}
  .back-phones{position:absolute;left:34px;top:292px;font-size:14px;line-height:1.4}
  .back-web{position:absolute;right:34px;top:300px;text-align:right;font-size:15px;line-height:1.35}

  /* Front: doctor side */
  .card--front{left:60px;top:440px}
  .wave{position:absolute;left:0;top:0}
  .practice-name{position:absolute;left:0;right:0;top:26px;text-align:center;font-size:34px;font-weight:700;color:var(--olive)}
  .doctor{position:absolute;left:40px;top:88px}
  .doctor-name{font-size:22px;font-weight:700;color:var(--olive)}
  .doctor-cred{font-size:15px;color:#6b6a60}
  .contact-list{position:absolute;right:34px;top:196px;list-style:none;color:var(--on-dark);font-size:17px;line-height:26px;text-align:right}
  .contact-list li{display:flex;justify-content:flex-end;align-items:center;gap:8px}
  .contact-list .icon{width:17px;height:17px;background:var(--on-dark);display:inline-flex;align-items:center;justify-content:center}
  .contact-list .icon-spacer{width:17px;display:inline-block}
  .address{position:absolute;left:40px;bottom:22px;font-size:18px;color:var(--on-dark)}
</style>
</head>
<body>

<section class="card card--back" aria-label="Appointment card back">
  <svg class="pen-icon" width="40" height="44" viewBox="0 0 40 44" aria-hidden="true">
    <path d="M4 2 L10 0 L36 36 L34 42 L30 40 Z" fill="var(--ink)"/>
  </svg>
  <h2 class="appt-title">Appoinment</h2>
  <div class="field field--for"><span>For:</span><span class="rule"></span></div>
  <div class="field field--date"><span>Date:</span><span class="rule"></span></div>
  <div class="days">
    <span class="day"><span class="box"></span>Mon</span>
    <span class="day"><span class="box"></span>Tue</span>
    <span class="day"><span class="box"></span>Wed</span>
    <span class="day"><span class="box"></span>Thu</span>
    <span class="day"><span class="box"></span>Fri</span>
    <span class="day"><span class="box"></span>Sat</span>
    <span class="day"><span class="box"></span>Sun</span>
  </div>
  <div class="day-rule"></div>
  <div class="field field--time"><span>Time:</span><span class="rule"></span></div>
  <p class="notice">If you are unable to keep your appoinment,<br>please contact us as soon as posible.</p>
  <div class="back-phones">(973) 555-0148<br>(973) 555.0162</div>
  <div class="back-web">www.gentlereliefpc.com<br>grpcare.service@inboxmail.com</div>
</section>

<section class="card card--front" aria-label="Business card front">
  <svg class="wave" width="640" height="366" viewBox="0 0 640 366" aria-hidden="true">
    <path d="M0,150 C150,112 330,124 470,150 S610,182 640,172" fill="none" stroke="var(--olive)" stroke-width="3"/>
    <path d="M0,176 C150,140 330,150 460,175 S600,205 640,200 L640,366 L0,366 Z" fill="var(--olive)"/>
    <path d="M0,176 C150,140 330,150 460,175 S600,205 640,200" fill="none" stroke="var(--olive-dark)" stroke-width="2"/>
    <path d="M20,178 C170,152 340,160 470,180 S600,205 630,196" fill="none" stroke="var(--paper)" stroke-width="4" stroke-linecap="round"/>
  </svg>
  <h1 class="practice-name">Gentle Relief Pain Care</h1>
  <div class="doctor">
    <div class="doctor-name">Dr. Lianwei Zhou</div>
    <div class="doctor-cred">M.D., Ph.D.</div>
  </div>
  <ul class="contact-list">
    <li>grpcare.service@inboxmail.com<span class="icon-spacer"></span></li>
    <li>(973) 555-0148
      <span class="icon"><svg width="11" height="11" viewBox="0 0 12 12" aria-hidden="true"><path d="M2 1 L4.5 1 L5.5 4 L4 5 C5 7 6 8 7.5 8.5 L8.5 7 L11 8 L11 10.5 C6 11 1 6 2 1Z" fill="var(--olive)"/></svg></span></li>
    <li>(973) 555.0162
      <span class="icon"><svg width="12" height="11" viewBox="0 0 12 11" aria-hidden="true"><rect x="1" y="4" width="10" height="6" fill="var(--olive)"/><rect x="3" y="1" width="6" height="3" fill="var(--olive)"/></svg></span></li>
    <li>grpcare.service@inboxmail.com
      <span class="icon"><svg width="12" height="9" viewBox="0 0 12 9" aria-hidden="true"><rect x="0.5" y="0.5" width="11" height="8" fill="none" stroke="var(--olive)"/><path d="M0.5 0.5 L6 5 L11.5 0.5" fill="none" stroke="var(--olive)"/></svg></span></li>
    <li>www.gentlereliefpc.com
      <span class="icon"><svg width="12" height="12" viewBox="0 0 12 12" aria-hidden="true"><circle cx="6" cy="6" r="5" fill="none" stroke="var(--olive)"/><path d="M1 6 H11 M6 1 V11" stroke="var(--olive)"/></svg></span></li>
  </ul>
  <p class="address">18 Corvell Road, Suite 304, Brisdale, NJ 07391</p>
</section>

</body>
</html>
```